Harrow Grading LLC business card design

Excavation company business cards

Contact Information for Business Card

Harrow Grading LLC cell phone 208-417-6290 office phone 208-319-4856 harrowgradingllc@maplecove.com Driveways, site prep, retaining walls, septic systems, rock delivery

Colors

Designer to choose colors to be used in the design.

```html
<!DOCTYPE html>
<html lang="en">
<head>
<meta charset="utf-8">
<title>Harrow Grading LLC — Business Cards</title>
<link href="https://fonts.googleapis.com/css2?family=Open+Sans:wght@400;600;700&display=swap" rel="stylesheet">
<style>
  :root {
    --stage: #1c1c1e;
    --card: #0f0f10;
    --accent: #e8701f;
    --ink-light: #f2f2f2;
    --ink-muted: #bdbdbd;
    --rule: #3a3a3a;
  }
  * { margin: 0; padding: 0; box-sizing: border-box; }
  html, body { width: 1200px; height: 900px; overflow: hidden; }
  body {
    background: var(--stage);
    font-family: "Open Sans", Arial, sans-serif;
    position: relative;
  }
  .card {
    position: absolute;
    width: 560px;
    height: 320px;
    background: var(--card);
    border-radius: 18px;
    overflow: hidden;
    box-shadow: 0 14px 30px rgba(0,0,0,.55);
  }
  .card--back { left: 590px; top: 90px; }
  .card--front { left: 50px; top: 490px; }

  .band {
    position: absolute;
    left: 0; right: 0;
    background: var(--accent);
    color: var(--ink-light);
    display: flex;
    flex-direction: column;
    align-items: center;
    justify-content: center;
    text-align: center;
  }

  /* brand name set as text */
  .brand {
    display: flex;
    align-items: center;
    gap: 10px;
    font-weight: 700;
    letter-spacing: 1px;
    line-height: 1.05;
  }
  .brand__mark { width: 14px; height: 14px; background: currentColor; flex: none; }

  /* back */
  .card--back .brand {
    position: absolute;
    left: 0; right: 0; top: 70px;
    justify-content: center;
    color: var(--ink-light);
    font-size: 34px;
  }
  .card--back .band { top: 200px; height: 62px; font-size: 14px; line-height: 1.45; }

  /* front */
  .card--front .brand {
    position: absolute;
    left: 30px; top: 100px;
    width: 210px;
    color: var(--accent);
    font-size: 22px;
  }
  .divider {
    position: absolute;
    left: 258px; top: 40px;
    width: 1px; height: 160px;
    background: var(--rule);
  }
  .contact { position: absolute; left: 280px; top: 44px; color: var(--ink-light); }
  .contact__name { color: var(--accent); font-size: 20px; font-weight: 600; letter-spacing: .3px; }
  .contact__title { font-size: 14px; margin-bottom: 18px; }
  .contact__list { list-style: none; font-size: 14px; }
  .contact__list li { display: flex; align-items: center; gap: 10px; height: 24px; }
  .contact__list svg { width: 15px; height: 15px; flex: none; }
  .card--front .band { top: 228px; height: 44px; font-size: 16px; }
</style>
</head>
<body>

  <section class="card card--back" aria-label="Business card, back">
    <div class="brand"><span class="brand__mark"></span>HARROW GRADING LLC</div>
    <div class="band">
      <span>Driveways • Site prep • Retaining walls</span>
      <span>Septic systems • Rock delivery</span>
    </div>
  </section>

  <section class="card card--front" aria-label="Business card, front">
    <div class="brand"><span class="brand__mark"></span>HARROW GRADING LLC</div>
    <div class="divider"></div>
    <div class="contact">
      <p class="contact__name">DANIEL REEVE</p>
      <p class="contact__title">Managing Director</p>
      <ul class="contact__list">
        <li>
          <svg viewBox="0 0 16 16" aria-hidden="true"><rect x="4" y="1" width="8" height="14" rx="1.5" fill="none" stroke="#e8701f" stroke-width="1.5"/><circle cx="8" cy="12.5" r="0.9" fill="#e8701f"/></svg>
          208-417-6290
        </li>
        <li>
          <svg viewBox="0 0 16 16" aria-hidden="true"><path d="M3.5 1.5l2.5 0 1 3.5-1.6 1.2c.8 1.8 2.2 3.2 4 4l1.2-1.6 3.5 1v2.5c0 .8-.7 1.5-1.5 1.4C7 13.1 2.9 9 2.5 3c-.1-.8.6-1.5 1-1.5z" fill="#e8701f"/></svg>
          208-319-4856
        </li>
        <li>
          <svg viewBox="0 0 16 16" aria-hidden="true"><rect x="1" y="3.5" width="14" height="9" fill="#e8701f"/><path d="M1 3.5l7 5 7-5" fill="none" stroke="#0f0f10" stroke-width="1.2"/></svg>
          harrowgradingllc@maplecove.com
        </li>
      </ul>
    </div>
    <div class="band">421, Address line goes here, 45452, Country Name</div>
  </section>

</body>
</html>
```